Professional and creative business card design for recruiting service providers

Our company supports German medium-sized companies in filling vacancies promptly. For this we use social media marketing and bring our customers into the visibility.

We want a professional but also creative design for our business cards.

Please look at lindqvar-staff.de to get an impression of our CI.

Target Market(s)

Small and medium-sized companies in Germany from the industry

Industry/Entity Type

Industrie, Handwerk

Contact Information for Business Card

Name, Position, Telefonnummer, Email, Website

Colors
EE7325
F08F49
F5BC92
FAE3D3
FDF4ED

Requirements
Must have
• A picture of the employee and in the style of www.lindqvar-staff.de

```html
<!DOCTYPE html>
<html lang="de">
<head>
<meta charset="utf-8">
<title>Lindqvar &amp; Staff – Visitenkarte</title>
<link href="https://fonts.googleapis.com/css2?family=Montserrat:wght@700&family=Arimo:wght@400&display=swap" rel="stylesheet">
<style>
  :root {
    --backdrop: #e6e6e6;
    --card-white: #ffffff;
    --card-dark: #333333;
    --ink: #2b2b2b;
    --ink-soft: #3a3a3a;
    --accent: #ee7325;
    --on-dark: #ffffff;
    --shape-grey: #d8d8d8;
  }
  html, body {
    margin: 0;
    width: 1200px;
    height: 802px;
    overflow: hidden;
    background: var(--backdrop);
  }
  .stage {
    position: relative;
    width: 1200px;
    height: 802px;
  }
  .card {
    position: absolute;
    top: 246px;
    width: 540px;
    height: 310px;
    box-shadow: 0 10px 24px rgba(0,0,0,0.18);
    overflow: hidden;
  }
  .card--front { left: 45px; background: var(--card-white); }
  .card--back  { left: 615px; background: var(--card-dark); }

  /* front */
  .brand {
    position: absolute;
    left: 30px;
    top: 40px;
    display: flex;
    align-items: center;
    gap: 12px;
  }
  .brand__square {
    width: 34px;
    height: 34px;
    background: var(--accent);
  }
  .brand__name {
    font-family: "Montserrat", sans-serif;
    font-weight: 700;
    font-size: 21px;
    line-height: 1.05;
    letter-spacing: 1.5px;
    color: var(--ink);
    text-transform: uppercase;
  }
  .person {
    position: absolute;
    left: 30px;
    top: 112px;
    font-family: "Arimo", sans-serif;
  }
  .person__name {
    margin: 0;
    font-size: 19px;
    font-weight: 400;
    color: var(--accent);
    letter-spacing: 0.5px;
    text-transform: uppercase;
  }
  .person__role {
    margin: 2px 0 0;
    font-size: 14px;
    color: var(--ink-soft);
  }
  .address {
    position: absolute;
    left: 30px;
    top: 172px;
    margin: 0;
    font-family: "Arimo", sans-serif;
    font-style: normal;
    font-size: 13px;
    line-height: 1.35;
    color: var(--ink-soft);
  }
  .contact {
    position: absolute;
    left: 30px;
    top: 220px;
    margin: 0;
    padding: 0;
    list-style: none;
    font-family: "Arimo", sans-serif;
    font-size: 13px;
    line-height: 1.55;
    color: var(--ink-soft);
  }
  .contact li { display: flex; align-items: center; gap: 8px; }
  .contact svg { width: 12px; height: 12px; flex: none; }

  .portrait {
    position: absolute;
    right: 0;
    top: 0;
    width: 250px;
    height: 310px;
    background: linear-gradient(180deg, #e9e9e9 0%, #d9d9d9 30%, #2a2a2e 55%, #16161a 100%);
  }

  /* back */
  .back-shape {
    position: absolute;
    left: 40px;
    top: 70px;
    width: 170px;
    height: 170px;
    background: linear-gradient(135deg, #4a4a4a, #2c2c2c);
  }
  .back-name {
    position: absolute;
    right: 40px;
    bottom: 48px;
    margin: 0;
    font-family: "Montserrat", sans-serif;
    font-weight: 700;
    font-size: 30px;
    line-height: 1.1;
    letter-spacing: 3px;
    color: var(--on-dark);
    text-transform: uppercase;
  }
</style>
</head>
<body>
<main class="stage">

  <section class="card card--front" aria-label="Vorderseite">
    <div class="brand">
      <span class="brand__square" aria-hidden="true"></span>
      <span class="brand__name">Lindqvar<br>&amp; Staff</span>
    </div>

    <div class="person">
      <h1 class="person__name">Jonas Brenner</h1>
      <p class="person__role">Manager</p>
    </div>

    <address class="address">Lindenweg 42b<br>70173 Stuttgart</address>

    <ul class="contact">
      <li>
        <svg viewBox="0 0 12 12" aria-hidden="true"><path d="M2.5 1 L4.5 1 L5.2 3.6 L4 4.6 Q5 7 7.4 8 L8.4 6.8 L11 7.5 L11 9.5 Q10.5 11 9 11 Q1 10 1 2.5 Q1 1 2.5 1Z" fill="var(--accent)"/></svg>
        <span>0170 555 2184</span>
      </li>
      <li>
        <svg viewBox="0 0 12 12" aria-hidden="true"><rect x="1" y="2.5" width="10" height="7" fill="none" stroke="var(--accent)" stroke-width="1.2"/><path d="M1 2.5 L6 6.5 L11 2.5" fill="none" stroke="var(--accent)" stroke-width="1.2"/></svg>
        <span>info@lindqvar-staff.de</span>
      </li>
      <li>
        <svg viewBox="0 0 12 12" aria-hidden="true"><circle cx="6" cy="6" r="5" fill="none" stroke="var(--accent)" stroke-width="1.2"/><ellipse cx="6" cy="6" rx="2.2" ry="5" fill="none" stroke="var(--accent)" stroke-width="1"/><path d="M1 6 H11" stroke="var(--accent)" stroke-width="1"/></svg>
        <span>www.lindqvar-staff.de</span>
      </li>
    </ul>

    <div class="portrait" role="img" aria-label="Porträtfoto des Mitarbeiters in dunklem Sakko und Rollkragenpullover"></div>
  </section>

  <section class="card card--back" aria-label="Rückseite">
    <div class="back-shape" aria-hidden="true"></div>
    <p class="back-name">Lindqvar<br>&amp; Staff</p>
  </section>

</main>
</body>
</html>
```